Animation College website

Name of College: Brightloom Academy of 3D Animation and VFX

We need a redesigned modern website for Tessmoor. The web-design should communicate a VFX and animation school and education. We will also need full access to the website once completed. We will also need access to the website to be able to make changes to the content and site ideally the website would be built on Wordpress.

To learn more about what the College please visit: http://brightloom-academy.example/
The video on the homepage demonstrates why Tessmoor is a unique college offering 3D animation and VFX. The direct link to the video can be watched here: https://videohost.example/482915036

Client Profile Summary: Tessmoor is an improved concept in job skills training for the 3D animation and visual effects industries. Our high graduate job placement numbers are based on the assertion that job skills must include more than simply learning to use software tools. Where nearly every digital media program teaches tools, job skills training should be about learning how to do a job in addition to learning how to use software tools. Tessmoor is taught in an apprenticeship style with very experienced faculty mentoring and teaching students to learn how to master their craft (VFX and animation) so they can seamlessly step into industry and excel.

Target Market(s)

High school students, students interested in learning about animation and 3D.

Industry/Entity Type

College

Coding

Coded - Design and coding required

Number of Pages Required

5+ page

Font styles to use
Sans Serif

Colors

Designer to choose colors to be used in the design.

Requirements
Must have
• Please include the video on the current Brightloom-academy.example website. https://videohost.example/482915036
• Use the same content on the current brightloom-academy.example website.
• Include a page to showcase student work.
• Website must also be mobile responsive.
Should not have
• The attached PDF of the landing page is just an example of something we like. You do not have to replicate this. The PDF landing page is showing the colour blue you should incorporate.

```html
<!DOCTYPE html>
<html lang="en">
<head>
<meta charset="utf-8">
<title>Tessmoor Academy of 3D Animation and VFX</title>
<link rel="stylesheet" href="https://fonts.googleapis.com/css2?family=Nunito+Sans:ital,wght@0,400;0,600;0,700;1,400&family=Open+Sans:ital,wght@0,400;0,600;1,400&display=swap">
<style>
:root{
  --blue:#1565b5;
  --blue-dark:#0f4f93;
  --blue-bright:#1e9be9;
  --ink:#2b2b2b;
  --grey-bg:#ededed;
  --white:#fff;
}
*{box-sizing:border-box;margin:0;padding:0}
html,body{width:1200px;height:3396px;overflow:hidden;background:var(--white)}
body{position:relative;font-family:"Nunito Sans",sans-serif;color:var(--ink)}
.abs{position:absolute}

/* hero */
.hero-photo{left:0;top:0;width:1200px;height:702px}
.brand{left:124px;top:30px;display:flex;align-items:center;gap:14px;color:var(--white);font-size:30px;font-weight:700}
.brand-mark{width:56px;height:56px;border-radius:50%;background:var(--white)}
.main-nav{left:435px;top:40px;display:flex;gap:21px;font-size:16px;color:var(--white);white-space:nowrap}
.hero-title{left:118px;top:336px;color:var(--white);font-size:32px;font-weight:700;line-height:41px}
.lead-form{left:736px;top:158px;width:351px;height:426px;background:var(--blue);padding:22px 29px}
.lead-form h2{color:var(--white);font-weight:400;font-size:25px;text-align:center;margin-bottom:16px}
.field{height:32px;background:var(--white);margin-bottom:7px;font-family:"Open Sans",sans-serif;font-size:12px;color:#999;padding:8px 10px;border-bottom:3px solid var(--blue-dark)}
.field.tall{height:72px}
.lead-form .send{margin-top:16px;height:40px;background:#0b0b0b;color:var(--white);font-weight:700;font-size:15px;text-align:center;line-height:40px}
.dots{left:558px;top:645px;display:flex;gap:7px}
.dots span{width:13px;height:13px;border-radius:50%;border:2px solid var(--white)}
.dots span.on{background:var(--white)}

/* intro */
.intro{left:0;top:762px;width:1200px;text-align:center}
.intro h1{font-size:36px;font-weight:400;color:#333}
.intro .sub{font-size:21px;color:#6b7a8a;margin-top:8px}
.body-copy{font-family:"Open Sans",sans-serif;font-size:14px;line-height:25px;color:#999}
.intro .body-copy{width:900px;margin:14px auto 0}
.badges{left:290px;top:1012px;display:flex;gap:78px;align-items:center}
.badge-round{width:106px;height:106px;border-radius:50%;border:4px solid #1f3f77;background:#e8edf5}
.badge-square{width:86px;height:86px;background:#f3dcd0}
.badge-square.red{background:#f6d4d4}

/* video */
.video-band{left:0;top:1330px;width:1200px;height:391px}
.video-player{left:310px;top:1225px;width:580px;height:362px;background:#1b1b1b;box-shadow:0 10px 30px rgba(0,0,0,.45)}
.video-still{left:0;top:0;width:580px;height:338px}
.video-caption{right:26px;top:90px;color:#dcdcdc;font-size:30px;font-weight:400}
.play{left:246px;top:130px}
.controls{left:0;top:338px;width:580px;height:24px;background:#0c0c0c}

/* split */
.split{left:0;top:1721px;width:1200px;height:498px;background:var(--grey-bg)}
.split-photo{left:0;top:0}
.split-copy{left:120px;top:94px;width:470px}
.split-copy h2{font-size:27px;font-weight:600;line-height:32px;color:#222}
.split-copy .tag{font-size:14.5px;color:var(--blue);font-weight:600;margin-top:14px}
.checks{list-style:none;margin-top:16px}
.checks li{font-family:"Open Sans",sans-serif;font-size:13px;line-height:19px;color:#888;padding-left:18px;position:relative;margin-bottom:12px}
.checks li::before{content:"";position:absolute;left:2px;top:5px;border-left:6px solid var(--blue);border-top:4px solid transparent;border-bottom:4px solid transparent}
.btn-more{left:120px;top:373px;width:142px;height:39px;background:var(--blue-dark);color:var(--white);font-size:13px;font-weight:700;text-align:center;line-height:39px}

/* testimonial */
.testimonial{left:0;top:2219px;width:1200px;height:459px}
.testimonial-bg{left:0;top:0;width:1200px;height:459px}
.testimonial h2{left:0;top:56px;width:1200px;text-align:center;color:var(--white);font-size:27px;font-weight:400}
.quote-frame{left:217px;top:160px;width:766px;height:234px;border:1.5px solid rgba(255,255,255,.7)}
.avatar{left:557px;top:118px;width:86px;height:86px;border-radius:50%;border:3px solid var(--white);background:linear-gradient(#7a5444,#c9a08c)}
.quote{left:312px;top:218px;width:576px;text-align:center;color:var(--white);font-family:"Open Sans",sans-serif;font-style:italic;font-size:14px;line-height:26px}
.quote-mark{top:206px;color:var(--white);font-size:44px;font-weight:700;line-height:40px}
.person{left:0;top:310px;width:1200px;text-align:center;color:var(--white)}
.person b{display:block;font-size:19px;font-weight:600}
.person span{font-size:14px}

/* advantage */
.advantage{left:0;top:2738px;width:1200px;text-align:center}
.advantage h2{font-size:32px;font-weight:400;color:var(--blue)}
.advantage .sub{font-size:25px;color:#999;margin-top:2px}
.advantage .body-copy{width:880px;margin:14px auto 0}
.perks{top:2928px;list-style:none}
.perks li{font-family:"Open Sans",sans-serif;font-size:14px;color:#333;line-height:20px;margin-bottom:15px;padding-left:18px;position:relative}
.perks li::before{content:"";position:absolute;left:0;top:5px;width:7px;height:7px;border-right:2px solid var(--blue);border-bottom:2px solid var(--blue);transform:rotate(-45deg)}
.btn-start{left:487px;top:3095px;width:226px;height:50px;background:var(--blue-bright);color:var(--white);font-size:20px;text-align:center;line-height:50px}

/* footer */
.site-footer{left:0;top:3188px;width:1200px;height:208px;background:var(--blue);border-top:6px solid var(--blue-dark)}
.footer-nav{left:0;top:38px;width:1200px;display:flex;justify-content:center;gap:44px;color:var(--white);font-size:20px}
.footer-note{left:0;top:86px;width:1200px;text-align:center;color:#d8e6f5;font-family:"Open Sans",sans-serif;font-size:14px}
.socials{left:0;top:120px;width:1200px;display:flex;justify-content:center;gap:8px}
.socials span{width:36px;height:36px;border-radius:50%;border:2px solid var(--white)}
</style>
</head>
<body>

<svg class="abs hero-photo" width="1200" height="702" role="img" aria-label="Photo of a student working at dual monitors in an animation studio">
  <defs>
    <linearGradient id="heroTone" x1="0" y1="0" x2="1" y2="1">
      <stop offset="0" stop-color="#3a4450"/>
      <stop offset=".55" stop-color="#1f252d"/>
      <stop offset="1" stop-color="#0d1014"/>
    </linearGradient>
  </defs>
  <polygon points="0,0 1200,0 1200,622 600,702 0,622" fill="url(#heroTone)"/>
</svg>

<div class="abs brand"><span class="brand-mark"></span>Tessmoor</div>
<nav class="abs main-nav">
  <span>How to Pick a School</span><span>Admission</span><span>Training</span><span>Philsophy</span><span>Faculty &amp; Staff</span><span>Apply</span>
</nav>
<h1 class="abs hero-title">3D Animation &amp; VFX One Year<br>Intensive Training Program</h1>

<form class="abs lead-form">
  <h2>Want to Know More?</h2>
  <div class="field">First Name</div>
  <div class="field">Last Name</div>
  <div class="field">Phone</div>
  <div class="field">Email</div>
  <div class="field">Country</div>
  <div class="field tall">Comments</div>
  <div class="send">SEND ME FREE INFO</div>
</form>
<div class="abs dots"><span></span><span class="on"></span><span class="on"></span><span class="on"></span></div>

<section class="abs intro">
  <h1>One Year Intensive Training Program</h1>
  <p class="sub">An Exciting, comprehensive Program with a 100% graduate employment rate</p>
  <p class="body-copy">Pellentesque faucibus Ut accumsan ultricies elit Maecenas at justo id velit placerat molestie Donec dictum lectus non odio Cras a ante vitae enim iaculis aliquam Mauris nunc quam venenatis nec euismod sit amet egestas placerat est Pellentesque habitant morbi tristique senectus et netus et malesuada fames ac turpis egestas Cras id elit Integer quis urna Ut ante enim dapibus malesuada fringilla eu condimentum quis tellus tros vel dolor Donec convallis pede venenatis nibh Duis</p>
</section>
<div class="abs badges">
  <span class="badge-round"></span>
  <span class="badge-round" style="border-color:#2a5f9e;background:#f4f6f9"></span>
  <span class="badge-square"></span>
  <span class="badge-square red"></span>
</div>

<svg class="abs video-band" width="1200" height="391" role="img" aria-label="Blue-tinted photo of a computer lab with monitors">
  <defs>
    <linearGradient id="bandTone" x1="0" y1="0" x2="1" y2="0">
      <stop offset="0" stop-color="#2d6ab8"/>
      <stop offset=".5" stop-color="#1a58aa"/>
      <stop offset="1" stop-color="#2f74c4"/>
    </linearGradient>
  </defs>
  <polygon points="0,40 600,0 1200,40 1200,391 0,391" fill="url(#bandTone)"/>
</svg>
<div class="abs video-player">
  <svg class="abs video-still" width="580" height="338" role="img" aria-label="Video still of a student speaking in a studio">
    <defs>
      <linearGradient id="stillTone" x1="0" y1="0" x2="1" y2="0">
        <stop offset="0" stop-color="#5a4a42"/>
        <stop offset=".5" stop-color="#2e3136"/>
        <stop offset="1" stop-color="#3d4650"/>
      </linearGradient>
    </defs>
    <rect width="580" height="338" fill="url(#stillTone)"/>
  </svg>
  <div class="abs video-caption">Phenomenal</div>
  <svg class="abs play" width="88" height="88">
    <circle cx="44" cy="44" r="41" fill="rgba(0,0,0,.25)" stroke="#fff" stroke-width="3"/>
    <polygon points="37,28 61,44 37,60" fill="none" stroke="#fff" stroke-width="3"/>
  </svg>
  <svg class="abs controls" width="580" height="24">
    <polygon points="14,6 24,12 14,18" fill="#fff"/>
    <rect x="44" y="11" width="430" height="3" fill="#fff"/>
    <rect x="498" y="14" width="3" height="4" fill="#1e9be9"/><rect x="503" y="11" width="3" height="7" fill="#1e9be9"/><rect x="508" y="8" width="3" height="10" fill="#1e9be9"/>
    <rect x="540" y="7" width="4" height="4" fill="#fff"/><rect x="548" y="7" width="4" height="4" fill="#fff"/><rect x="540" y="14" width="4" height="4" fill="#fff"/><rect x="548" y="14" width="4" height="4" fill="#fff"/>
  </svg>
</div>

<section class="abs split">
  <svg class="abs split-photo" width="1200" height="498" role="img" aria-label="Photo of a smiling student at a workstation lit by warm screen light">
    <defs>
      <linearGradient id="splitTone" x1="0" y1="0" x2="1" y2="1">
        <stop offset="0" stop-color="#7a3a5a"/>
        <stop offset=".45" stop-color="#3b2a35"/>
        <stop offset="1" stop-color="#8a5a2c"/>
      </linearGradient>
    </defs>
    <polygon points="543,0 1200,0 1200,498 668,498" fill="url(#splitTone)"/>
  </svg>
  <div class="abs split-copy">
    <h2>Learn Animation &amp; Visual Effects Production from the Experts</h2>
    <p class="tag">The worlds first and sole simulated production training Program</p>
    <ul class="checks">
      <li>Core skills: An intensive introduction to skills involving cameras, modeling, animation, dynamics, lighting, composition, production and more</li>
      <li>Transition into practice: Expand on core skills with advanced training and team Production</li>
      <li>Practical Training: Practical hands-on production and dailies training</li>
    </ul>
  </div>
  <div class="abs btn-more">READ MORE</div>
</section>

<section class="abs testimonial">
  <svg class="abs testimonial-bg" width="1200" height="459" role="img" aria-label="Dim, blurred photo of students in a classroom">
    <defs>
      <radialGradient id="quoteTone" cx=".5" cy=".5" r=".7">
        <stop offset="0" stop-color="#3a3530"/>
        <stop offset="1" stop-color="#121212"/>
      </radialGradient>
    </defs>
    <rect width="1200" height="459" fill="url(#quoteTone)"/>
  </svg>
  <h2 class="abs">What Our Student Says</h2>
  <div class="abs quote-frame"></div>
  <div class="abs avatar" role="img" aria-label="Portrait of the student quoted"></div>
  <span class="abs quote-mark" style="left:282px">&ldquo;</span>
  <span class="abs quote-mark" style="left:898px">&rdquo;</span>
  <p class="abs quote">You're going to sit down with someone who's in industry, who's professional, who is going to teach you how to be in that position. And you're working with other people who are as passionate as you and who want to learn as much as you do.</p>
  <div class="abs person"><b>Nora Pell</b><span>CG Generalist, Kitefield Studios</span></div>
  <svg class="abs" style="left:160px;top:236px" width="28" height="64"><polyline points="24,2 4,32 24,62" fill="none" stroke="#fff" stroke-width="2"/></svg>
  <svg class="abs" style="left:1006px;top:236px" width="28" height="64"><polyline points="4,2 24,32 4,62" fill="none" stroke="#fff" stroke-width="2"/></svg>
</section>

<section class="abs advantage">
  <h2>The Tessmoor Advantage</h2>
  <p class="sub">A Program designed by industry for industry</p>
  <p class="body-copy">arcu Morbi porta libero id ullamcorper nonummy nibh ligula pulvinar metus eget consectetuer augue nisi quis lacus Ut ac mi quis lacus mollis aliquam Curabitur iaculis tempus eros Curabitur vel mi sit amet magna malesuada ultrices , Morbi ornare gravida elit Integer congue augue et</p>
</section>
<ul class="abs perks" style="left:245px">
  <li>Affordable tutuion for both domestic and international students</li>
  <li>A faculty of 12 world class industry masters</li>
  <li>Maximum class size of 12 students</li>
  <li>One-on-one Mentorship</li>
</ul>
<ul class="abs perks" style="left:747px">
  <li>Employment Opportunities</li>
  <li>Scholarships</li>
  <li>And more</li>
</ul>
<div class="abs btn-start">Get Started Now &rsaquo;</div>

<footer class="abs site-footer">
  <nav class="abs footer-nav">
    <span>How to Pick a School</span><span>Admission</span><span>Training</span><span>Philsophy</span><span>Faculty &amp; Staff</span><span>Apply</span>
  </nav>
  <p class="abs footer-note">&copy; 2017 Company Name &nbsp;All right reserved &nbsp;Term of Use</p>
  <div class="abs socials"><span></span><span></span><span></span><span></span><span></span><span></span></div>
</footer>

</body>
</html>
```